I need a business card designed using the logo provided either vertical or horizontal......Harbourline Property Group is an Australian based real estate company that caters for the upper end of the market so the design of the business card "must reflect" the companies image!!
Colour combinations are optional but "must be realistic" and must be able to be accurately useable CMYK colours.
Please consider that any colours used "must be able to be used" and be suitable in following designs for "pull out banner signs" and "real estate signs".
The colours and the font in the attached designs are for example and other combinations are encouraged.
Target Market(s)
The High End of the Australian real estate market
Industry/Entity Type
Business
Contact Information for Business Card
Logo - Business Name - Director + Licensed Real Estate Agent - Mobile Number (Cell Phone) - Business Number - Fax - Email Address - Web address
Requirements
Must have
- Designs and colours (CMYK) that can easily be interpreted by an Australian printer.
Nice to have
- Some alternative ideas on colour and font..........the ones provided are ok and have been provided as an example but I am looking for alternative ideas
Should not have
- Loud, overly bright colours. Designs that do not reflect the professional standards of the business.
- Designs that look good on a computer monitor but can not be re-created on a printing press.............this is most important when it comes to shading etc.

```html
<!DOCTYPE html>
<html lang="en">
<head>
<meta charset="utf-8">
<title>Harbourline Property Group – Business Card</title>
<link rel="stylesheet" href="https://fonts.googleapis.com/css2?family=Open+Sans:wght@400;600;700&display=swap">
<style>
  :root {
    --backdrop: #8e8e8c;
    --mustard: #b27d2a;
    --sand: #d9cfa6;
    --cream: #f3eedc;
    --ink: #1f1d1a;
    --white: #ffffff;
    --card-w: 700px;
    --card-h: 400px;
  }
  * { box-sizing: border-box; margin: 0; padding: 0; }
  html, body {
    width: 1200px;
    height: 900px;
    overflow: hidden;
    background: var(--backdrop);
    font-family: "Open Sans", Arial, sans-serif;
  }
  .sheet {
    position: relative;
    width: 1200px;
    height: 900px;
  }
  .card {
    position: absolute;
    left: 250px;
    width: var(--card-w);
    height: var(--card-h);
    overflow: hidden;
    box-shadow: 0 6px 18px rgba(0,0,0,0.25);
  }

  /* Brand side */
  .card--brand { top: 40px; background: var(--sand); }
  .card--brand .brand-band {
    position: absolute;
    left: 0; right: 0;
    top: 90px; height: 260px;
    background: var(--mustard);
    display: flex;
    align-items: center;
    justify-content: center;
  }
  .wordmark {
    font-weight: 600;
    text-transform: uppercase;
    line-height: 1.1;
    text-align: left;
  }
  .wordmark__line { display: block; }
  .wordmark__line--main { font-size: 40px; letter-spacing: 3px; }
  .wordmark__line--sub { font-size: 22px; letter-spacing: 9px; }
  .card--brand .wordmark { color: var(--white); }

  /* Contact side */
  .card--contact { top: 460px; background: var(--cream); }
  .card--contact .wordmark-area {
    position: absolute;
    left: 0; right: 0;
    top: 0; height: 210px;
    display: flex;
    align-items: center;
    justify-content: center;
    padding-left: 140px;
  }
  .card--contact .wordmark { color: var(--ink); }
  .card--contact .wordmark__line--main { font-size: 34px; letter-spacing: 2px; }
  .card--contact .wordmark__line--sub { font-size: 19px; letter-spacing: 7px; }

  .contact-band {
    position: absolute;
    left: 0; right: 0;
    top: 210px; height: 152px;
    background: var(--mustard);
    color: var(--white);
  }
  .person {
    position: absolute;
    left: 30px;
    top: 12px;
  }
  .person__name { font-size: 22px; font-weight: 700; }
  .person__role { font-size: 13px; font-weight: 400; }

  .contact-list {
    position: absolute;
    right: 26px;
    top: 34px;
    list-style: none;
    text-align: right;
    font-size: 15px;
    line-height: 22px;
  }
  .contact-list li {
    display: flex;
    justify-content: flex-end;
    align-items: center;
    gap: 8px;
  }
  .icon { width: 13px; height: 13px; fill: var(--white); flex: none; }
</style>
</head>
<body>
<main class="sheet">

  <section class="card card--brand" aria-label="Business card, brand side">
    <div class="brand-band">
      <div class="wordmark">
        <span class="wordmark__line wordmark__line--main">Harbourline</span>
        <span class="wordmark__line wordmark__line--sub">Property Group</span>
      </div>
    </div>
  </section>

  <section class="card card--contact" aria-label="Business card, contact side">
    <div class="wordmark-area">
      <div class="wordmark">
        <span class="wordmark__line wordmark__line--main">Harbourline</span>
        <span class="wordmark__line wordmark__line--sub">Property Group</span>
      </div>
    </div>

    <div class="contact-band">
      <div class="person">
        <p class="person__name">Daniel Whitford</p>
        <p class="person__role">Managing Director</p>
      </div>

      <ul class="contact-list">
        <li>0412 555 018
          <svg class="icon" viewBox="0 0 16 16" aria-hidden="true"><path d="M3 1h3l1 4-2 1a9 9 0 0 0 5 5l1-2 4 1v3a2 2 0 0 1-2 2A13 13 0 0 1 1 3a2 2 0 0 1 2-2z"/></svg>
        </li>
        <li>02 5550 1234
          <svg class="icon" viewBox="0 0 16 16" aria-hidden="true"><path d="M4 0h8a1 1 0 0 1 1 1v14a1 1 0 0 1-1 1H4a1 1 0 0 1-1-1V1a1 1 0 0 1 1-1zm1 2v10h6V2zm3 11a1 1 0 1 0 0 2 1 1 0 0 0 0-2z"/></svg>
        </li>
        <li>info@harbourlinegroup.com.au
          <svg class="icon" viewBox="0 0 16 16" aria-hidden="true"><path d="M0 3h16v1L8 9 0 4zm0 3 8 5 8-5v7H0z"/></svg>
        </li>
        <li>www.harbourlinegroup.com.au
          <svg class="icon" viewBox="0 0 16 16" aria-hidden="true"><path d="M6.5 9.5l3-3M7 4l2-2a3 3 0 0 1 4 4l-2 2M9 12l-2 2a3 3 0 0 1-4-4l2-2" stroke="#fff" stroke-width="2" fill="none" stroke-linecap="round"/></svg>
        </li>
        <li>42 Wharf Street, Sydney NSW, Australia, 2000
          <svg class="icon" viewBox="0 0 16 16" aria-hidden="true"><path d="M8 0a5.5 5.5 0 0 0-5.5 5.5C2.5 10 8 16 8 16s5.5-6 5.5-10.5A5.5 5.5 0 0 0 8 0zm0 8a2.5 2.5 0 1 1 0-5 2.5 2.5 0 0 1 0 5z"/></svg>
        </li>
      </ul>
    </div>
  </section>

</main>
</body>
</html>
```